Modern Business Card

Modern professional business card with more than just logo and demographic info. Something memorable.

We are a trendy/modern chiropractic group with an emphasis on neurology, hence the minimalist-type brain logo. We want to convey that modern and technical aspect with professionalism and the elite nature of our practice environment.

```html
<!DOCTYPE html>
<html lang="en">
<head>
<meta charset="utf-8">
<title>Cortex Chiropractic – Business Card</title>
<link rel="stylesheet" href="https://fonts.googleapis.com/css2?family=Montserrat:wght@400;500&family=Oswald:wght@500&display=swap">
<style>
  :root {
    --backdrop: #dcdcdc;
    --card-dark: #1c1c1c;
    --card-light: #ffffff;
    --brand-blue: #4a80c6;
    --ink: #2b2b2b;
    --muted: #555555;
    --divider: #9a9a9a;
    --on-dark: #ffffff;
  }
  * { box-sizing: border-box; margin: 0; padding: 0; }
  html, body { width: 1200px; height: 930px; overflow: hidden; }
  body {
    background: var(--backdrop);
    font-family: "Montserrat", sans-serif;
    position: relative;
  }
  .card {
    position: absolute;
    width: 520px;
    height: 300px;
    border-radius: 22px;
    box-shadow: 0 8px 22px rgba(0,0,0,0.18);
    overflow: hidden;
  }
  .card--front { left: 70px; top: 150px; background: var(--card-dark); }
  .card--back { left: 610px; top: 480px; background: var(--card-light); }

  .brand {
    display: flex;
    align-items: center;
    gap: 14px;
  }
  .brand__dot {
    border-radius: 50%;
    background: var(--brand-blue);
    flex: none;
  }
  .brand__name {
    font-family: "Montserrat", sans-serif;
    font-weight: 500;
    text-transform: uppercase;
    line-height: 1.05;
  }
  .card--front .brand {
    position: absolute; left: 0; right: 0; top: 0; bottom: 0;
    justify-content: center;
  }
  .card--front .brand__dot { width: 58px; height: 58px; }
  .card--front .brand__name { color: var(--on-dark); font-size: 30px; letter-spacing: 2px; }

  .card--back .brand {
    position: absolute; left: 0; right: 0; top: 48px;
    justify-content: center;
    gap: 10px;
  }
  .card--back .brand__dot { width: 36px; height: 36px; }
  .card--back .brand__name { color: var(--ink); font-size: 18px; letter-spacing: 1.5px; }

  .holder {
    position: absolute;
    right: 295px;
    top: 134px;
    text-align: right;
  }
  .holder__name {
    font-family: "Oswald", sans-serif;
    font-weight: 500;
    color: var(--brand-blue);
    font-size: 26px;
    letter-spacing: 2px;
    text-transform: uppercase;
  }
  .holder__role { color: var(--muted); font-size: 12px; margin-top: 2px; }

  .divider {
    position: absolute;
    left: 250px; top: 118px;
    width: 1px; height: 76px;
    background: var(--divider);
  }

  .contacts {
    position: absolute;
    left: 272px; top: 122px;
    list-style: none;
    font-size: 13px;
    color: var(--ink);
  }
  .contacts li { display: flex; align-items: center; gap: 10px; height: 23px; }
  .contacts svg { width: 12px; height: 12px; flex: none; }

  .address-band {
    position: absolute;
    left: 0; right: 0; top: 236px;
    height: 30px;
    background: var(--brand-blue);
    color: var(--on-dark);
    font-size: 13px;
    display: flex;
    align-items: center;
    justify-content: center;
    letter-spacing: 0.3px;
  }
</style>
</head>
<body>
  <section class="card card--front" aria-label="Card front">
    <div class="brand">
      <span class="brand__dot"></span>
      <span class="brand__name">Cortex<br>Chiropractic</span>
    </div>
  </section>

  <section class="card card--back" aria-label="Card back">
    <div class="brand">
      <span class="brand__dot"></span>
      <span class="brand__name">Cortex<br>Chiropractic</span>
    </div>

    <div class="holder">
      <div class="holder__name">Marcus Hale</div>
      <div class="holder__role">Director</div>
    </div>

    <div class="divider"></div>

    <ul class="contacts">
      <li>
        <svg viewBox="0 0 24 24" aria-hidden="true"><path fill="var(--brand-blue)" d="M6.6 10.8a15.1 15.1 0 0 0 6.6 6.6l2.2-2.2a1 1 0 0 1 1-.25 11.4 11.4 0 0 0 3.6.57 1 1 0 0 1 1 1V20a1 1 0 0 1-1 1A17 17 0 0 1 3 4a1 1 0 0 1 1-1h3.5a1 1 0 0 1 1 1c0 1.25.2 2.45.57 3.57a1 1 0 0 1-.25 1z"/></svg>
        (555) 014-2093
      </li>
      <li>
        <svg viewBox="0 0 24 24" aria-hidden="true"><rect x="3" y="5" width="18" height="14" rx="2" fill="none" stroke="var(--brand-blue)" stroke-width="2.2"/><path d="M3 6l9 7 9-7" fill="none" stroke="var(--brand-blue)" stroke-width="2.2"/></svg>
        hello@cortexchiro.com
      </li>
      <li>
        <svg viewBox="0 0 24 24" aria-hidden="true"><circle cx="12" cy="12" r="9" fill="none" stroke="var(--brand-blue)" stroke-width="2.2"/><path d="M3 12h18M12 3c3 3.2 3 14.8 0 18M12 3c-3 3.2-3 14.8 0 18" fill="none" stroke="var(--brand-blue)" stroke-width="1.8"/></svg>
        www.cortexchiro.com
      </li>
    </ul>

    <div class="address-band">1187 Alder Ridge Road Salem, OR 97301</div>
  </section>
</body>
</html>
```